Web Calculator design Housing Investment

We have a web calculator that needs to be fixed from a design perspective. The key tasks are:<br/>1. Selecting icons / pictures / colours for the various steps<br/>2. Designing navigation between calculator steps<br/>3. Making suggestions for chart design. The limitation is that the charts are all using the Vextra API (the same charts that Vextra Grids use).<br/><br/>There are four entry screens and then a result screen. See attached PDF for screenshots. You can see our website at https://larkhollowfunds.com for our corporate colours and style.

Target Market(s)

Real Estate Investors

Industry/Entity Type

Financial Planning

Number of Pages Required

1 page

Font styles to use
Sans Serif
Other font styles liked:
• Ubuntu

Colors
86cae7
3176b5
0455a3
ffffff

Requirements
Must have
• New Icons
• Suggested design for navigation
• Suggested design for charts

```html
<!DOCTYPE html>
<html lang="en">
<head>
<meta charset="utf-8">
<title>Property Comparison Calculator – Lark Hollow Funds</title>
<link href="https://fonts.googleapis.com/css2?family=Ubuntu:wght@300;400;500;700&display=swap" rel="stylesheet">
<style>
:root{
  --navy:#0455a3;
  --mid:#3176b5;
  --sky:#86cae7;
  --map:#4db3f0;
  --white:#ffffff;
  --page:#f3f6f8;
  --ink:#3c3c3c;
  --muted:#7a7a7a;
  --track:#e2e4e6;
  --footer:#333333;
  --dash:#1d2226;
  --dash-panel:#262c31;
}
*{box-sizing:border-box;margin:0;padding:0}
html,body{width:1200px;height:3246px;overflow:hidden}
body{background:var(--page);font-family:'Ubuntu',sans-serif;color:var(--ink);position:relative}
.panel{position:absolute;left:93px;width:1013px;background:var(--white);box-shadow:0 2px 10px rgba(0,0,0,.04)}
.p1{top:72px;height:536px}
.p2{top:692px;height:536px}
.p3{top:1308px;height:536px}
.p4{top:1941px;height:595px}
.p5{top:2599px;height:575px}
.abs{position:absolute}

/* stepper */
.track{position:absolute;top:52px;left:59px;width:694px;height:2px;background:var(--track)}
.step{position:absolute;top:0;width:0}
.step-num{position:absolute;top:22px;left:-20px;width:40px;text-align:center;font-size:14px;color:var(--muted)}
.step-dot{position:absolute;top:46px;left:-7px;width:14px;height:14px;border-radius:50%;background:#e6e7e8;border:2px solid #f4f4f4}
.step-label{position:absolute;top:72px;left:-90px;width:180px;text-align:center;font-size:13px;color:var(--muted);font-weight:300}
.step.active .step-num,.step.active .step-label{color:var(--navy);font-weight:500}
.step.active .step-dot{background:var(--navy);border-color:var(--navy)}
.step.done .step-dot{background:var(--white);border:1.5px solid var(--navy);width:16px;height:16px;left:-8px;top:45px}
.step.done .step-dot svg{position:absolute;left:2px;top:2px}

.btn{position:absolute;top:34px;height:37px;border-radius:19px;font-size:15px;font-weight:700;display:flex;align-items:center;justify-content:center}
.btn-primary{background:var(--navy);color:var(--white)}
.btn-outline{border:1.5px solid var(--navy);color:var(--navy);background:var(--white)}

.footer{position:absolute;left:0;bottom:0;width:100%;height:50px;background:var(--footer);color:#d8d8d8;font-size:12px;font-weight:300;display:flex;align-items:center;justify-content:center;white-space:pre}
.footer .brand{color:var(--sky)}

.title{position:absolute;left:0;width:100%;text-align:center;font-size:29px;font-weight:300;color:#444;line-height:35px}

/* property type tiles */
.tile{position:absolute;top:233px;width:138px;height:153px;border:2px solid var(--navy);background:var(--navy)}
.tile.outline{background:var(--white)}
.tile-art{position:absolute;left:29px;top:14px;width:76px;height:76px;border-radius:4px}
.tile-label{position:absolute;left:0;bottom:0;width:100%;height:40px;background:var(--navy);color:var(--white);font-size:20px;display:flex;align-items:center;justify-content:center;border-top:1px solid rgba(255,255,255,.25)}

/* sliders */
.field-label{position:absolute;font-size:11px;color:#666;font-weight:300;display:flex;align-items:center;gap:5px}
.info{width:11px;height:11px;border:1px solid #888;border-radius:50%;font-size:8px;display:inline-flex;align-items:center;justify-content:center;color:#888}
.slider{position:absolute;height:2px;background:var(--track)}
.slider .fill{position:absolute;left:0;top:0;height:2px;background:var(--navy)}
.slider .knob{position:absolute;top:-4px;width:10px;height:10px;border-radius:50%;background:var(--navy)}
.slider-value{position:absolute;font-size:11px;color:#555}

/* method cards */
.method{position:absolute;top:0;width:260px;margin-left:-130px;text-align:center}
.diamond{position:absolute;top:237px;width:104px;height:104px;transform:rotate(45deg);border:1.5px solid var(--mid);border-radius:10px;background:var(--white);box-shadow:0 0 0 5px var(--white),0 0 0 6px #b9d3ea}
.method-art{position:absolute;top:264px;width:52px;height:52px;border-radius:50%}
.method-title{position:absolute;top:376px;left:0;width:100%;font-size:16px;font-weight:500;color:#333}
.method-text{position:absolute;top:403px;left:0;width:100%;font-size:12px;font-weight:300;color:#777;line-height:17px}

/* forecast */
.row-label{position:absolute;font-size:13px;font-weight:300;color:#666;text-align:right;line-height:17px}
.select{position:absolute;width:164px;height:37px;border:1px solid #cfd6dd;background:var(--white);font-size:13px;color:#888;display:flex;align-items:center;padding-left:10px}
.select .caret{position:absolute;right:0;top:-1px;width:34px;height:37px;background:var(--navy);display:flex;align-items:center;justify-content:center}
.chart-box{position:absolute;border:1px solid #e4e6e8;background:var(--white)}
.note{position:absolute;font-size:11px;font-weight:300;color:#777}

/* dashboard */
.dash{position:absolute;left:21px;top:158px;width:969px;height:126px;background:var(--dash);border-radius:2px}
.dash-form{position:absolute;left:10px;top:14px;width:300px;font-size:7px;color:#cfd4d8}
.dash-row{position:absolute;left:0;width:300px;height:14px}
.dash-row .lbl{position:absolute;right:160px;top:3px;white-space:nowrap}
.dash-select{position:absolute;left:143px;top:0;width:130px;height:13px;border:1px solid #4a5158;background:#1f2428;font-size:6px;padding-left:5px;line-height:11px;color:#dde}
.dash-chart{position:absolute;top:8px;height:108px;background:var(--dash-panel);border:1px solid #3a4147}
.dash-sum{position:absolute;left:811px;top:8px;width:150px;height:108px;background:var(--dash-panel);border:1px solid #3a4147;color:var(--white);text-align:center;font-size:9px}
.dash-sum .small{font-size:6.5px;color:#dfe3e6}
</style>
</head>
<body>

<!-- Step 1 -->
<section class="panel p1">
  <div class="track"></div>
  <div class="step active" style="left:59px"><div class="step-num">01</div><div class="step-dot"></div><div class="step-label" style="left:-79px">Property Type</div></div>
  <div class="step" style="left:239px"><div class="step-num">02</div><div class="step-dot"></div><div class="step-label">Property Location</div></div>
  <div class="step" style="left:408px"><div class="step-num">03</div><div class="step-dot"></div><div class="step-label">Property Valuation</div></div>
  <div class="step" style="left:580px"><div class="step-num">04</div><div class="step-dot"></div><div class="step-label" style="left:-94px">Your Property Forecast</div></div>
  <div class="step" style="left:752px"><div class="step-num">05</div><div class="step-dot"></div><div class="step-label" style="left:-99px;top:74px">Calculation</div></div>
  <div class="btn btn-primary" style="left:901px;width:92px">Next</div>

  <h1 class="title" style="top:142px">What type of property would<br>you like to compare?</h1>

  <div class="tile" style="left:363px">
    <div class="tile-art" role="img" aria-label="Illustration of an apartment block with residents" style="background:var(--mid)"></div>
    <div class="tile-label">Unit</div>
  </div>
  <div class="tile outline" style="left:508px">
    <div class="tile-art" role="img" aria-label="Illustration of a two-storey house" style="background:#d6ebf6"></div>
    <div class="tile-label">House</div>
  </div>

  <footer class="footer">© 2019 <span class="brand">Lark Hollow Funds</span>. All Right Reserved.</footer>
</section>

<!-- Step 2 -->
<section class="panel p2">
  <div class="track"></div>
  <div class="step done" style="left:59px"><div class="step-num">01</div><div class="step-dot"><svg width="10" height="10" viewBox="0 0 10 10"><path d="M2 5.2 4.2 7.4 8 3" fill="none" stroke="#0455a3" stroke-width="1.3"/></svg></div><div class="step-label" style="left:-79px">Property Type</div></div>
  <div class="step active" style="left:239px"><div class="step-num">02</div><div class="step-dot"></div><div class="step-label">Property Location</div></div>
  <div class="step" style="left:408px"><div class="step-num">03</div><div class="step-dot"></div><div class="step-label">Property Valuation</div></div>
  <div class="step" style="left:580px"><div class="step-num">04</div><div class="step-dot"></div><div class="step-label" style="left:-94px">Your Property Forecast</div></div>
  <div class="step" style="left:752px"><div class="step-num">05</div><div class="step-dot"></div><div class="step-label" style="left:-99px;top:74px">Calculation</div></div>
  <div class="btn btn-outline" style="left:801px;width:94px">Privious</div>
  <div class="btn btn-primary" style="left:901px;width:92px">Next</div>

  <h1 class="title" style="top:142px">Where would this property be located?</h1>

  <div class="abs" role="img" aria-label="Map of Australia with selectable states, Northern Territory highlighted" style="left:217px;top:235px;width:219px;height:202px;border-radius:40% 45% 40% 45%;background:linear-gradient(135deg,var(--map),#3ea6e6)"></div>

  <div class="field-label" style="left:478px;top:254px">How much will the property cost? <span class="info">i</span></div>
  <div class="slider" style="left:478px;top:283px;width:257px"><div class="fill" style="width:44px"></div><div class="knob" style="left:40px"></div></div>
  <div class="slider-value" style="left:745px;top:276px">$ 500,000</div>

  <div class="field-label" style="left:478px;top:331px">How much will you invest? <span class="info">i</span></div>
  <div class="slider" style="left:478px;top:360px;width:257px"><div class="fill" style="width:22px"></div><div class="knob" style="left:18px"></div></div>
  <div class="slider-value" style="left:745px;top:353px">$ 200,000</div>

  <footer class="footer">© 2019 <span class="brand">Lark Hollow Funds</span>. All Right Reserved.</footer>
</section>

<!-- Step 3 -->
<section class="panel p3">
  <div class="track"></div>
  <div class="step done" style="left:59px"><div class="step-num">01</div><div class="step-dot"><svg width="10" height="10" viewBox="0 0 10 10"><path d="M2 5.2 4.2 7.4 8 3" fill="none" stroke="#0455a3" stroke-width="1.3"/></svg></div><div class="step-label" style="left:-79px">Property Type</div></div>
  <div class="step done" style="left:239px"><div class="step-num">02</div><div class="step-dot"><svg width="10" height="10" viewBox="0 0 10 10"><path d="M2 5.2 4.2 7.4 8 3" fill="none" stroke="#0455a3" stroke-width="1.3"/></svg></div><div class="step-label">Property Location</div></div>
  <div class="step active" style="left:408px"><div class="step-num">03</div><div class="step-dot"></div><div class="step-label">Property Valuation</div></div>
  <div class="step" style="left:580px"><div class="step-num">04</div><div class="step-dot"></div><div class="step-label" style="left:-94px">Your Property Forecast</div></div>
  <div class="step" style="left:752px"><div class="step-num">05</div><div class="step-dot"></div><div class="step-label" style="left:-99px;top:74px">Calculation</div></div>
  <div class="btn btn-outline" style="left:801px;width:94px">Privious</div>
  <div class="btn btn-primary" style="left:901px;width:92px">Next</div>

  <h1 class="title" style="top:133px">How would you like to forecast the returns<br>from property?</h1>

  <div class="method" style="left:194px">
    <div class="diamond" style="left:78px"></div>
    <div class="method-art" role="img" aria-label="Illustration of a calculator with coins and a document" style="left:104px;background:linear-gradient(135deg,#f5b043,#3ba36b)"></div>
    <div class="method-title">Relative Cost</div>
    <div class="method-text">Use this to value property based on<br>mortgage cost relative to rent cost</div>
  </div>
  <div class="method" style="left:507px">
    <div class="diamond" style="left:78px"></div>
    <div class="method-art" role="img" aria-label="Illustration of a worker with a money bag" style="left:104px;background:linear-gradient(135deg,#e9a23b,#3f7fc1)"></div>
    <div class="method-title">Relative To Wages</div>
    <div class="method-text">Use this to value property based on<br>mortgage cost relative to bages</div>
  </div>
  <div class="method" style="left:821px">
    <div class="diamond" style="left:78px"></div>
    <div class="method-art" role="img" aria-label="Illustration of a percentage badge" style="left:104px;background:radial-gradient(circle,#e83b2f 45%,#f7b23a 70%)"></div>
    <div class="method-title">Using Rental Yield</div>
    <div class="method-text">Use this to value property based on<br>a rental yield</div>
  </div>

  <footer class="footer">© 2019 <span class="brand">Lark Hollow Funds</span>. All Right Reserved.</footer>
</section>

<!-- Step 4 -->
<section class="panel p4">
  <div class="track"></div>
  <div class="step done" style="left:59px"><div class="step-num">01</div><div class="step-dot"><svg width="10" height="10" viewBox="0 0 10 10"><path d="M2 5.2 4.2 7.4 8 3" fill="none" stroke="#0455a3" stroke-width="1.3"/></svg></div><div class="step-label" style="left:-79px">Property Type</div></div>
  <div class="step done" style="left:239px"><div class="step-num">02</div><div class="step-dot"><svg width="10" height="10" viewBox="0 0 10 10"><path d="M2 5.2 4.2 7.4 8 3" fill="none" stroke="#0455a3" stroke-width="1.3"/></svg></div><div class="step-label">Property Location</div></div>
  <div class="step done" style="left:408px"><div class="step-num">03</div><div class="step-dot"><svg width="10" height="10" viewBox="0 0 10 10"><path d="M2 5.2 4.2 7.4 8 3" fill="none" stroke="#0455a3" stroke-width="1.3"/></svg></div><div class="step-label">Property Valuation</div></div>
  <div class="step active" style="left:580px"><div class="step-num">04</div><div class="step-dot"></div><div class="step-label" style="left:-94px">Your Property Forecast</div></div>
  <div class="step" style="left:752px"><div class="step-num">05</div><div class="step-dot"></div><div class="step-label" style="left:-99px;top:74px">Calculation</div></div>
  <div class="btn btn-outline" style="left:801px;width:94px">Privious</div>
  <div class="btn btn-primary" style="left:901px;width:92px">Next</div>

  <h1 class="title" style="top:132px;font-weight:500;font-size:28px">Your Property price Forecast</h1>

  <div class="row-label" style="right:509px;top:194px">Your have chosen to forecast property prices using</div>
  <div class="select" style="left:515px;top:188px">Gross Tental Yield<span class="caret"><svg width="10" height="6" viewBox="0 0 10 6"><path d="M1 1l4 4 4-4" fill="none" stroke="#fff" stroke-width="1.3"/></svg></span></div>

  <div class="row-label" style="right:509px;top:245px">You can see how this ratio has charged over time (in blue)<br>below vs your assumption (in red) for</div>
  <div class="select" style="left:515px;top:238px">Sydney House<span class="caret"><svg width="10" height="6" viewBox="0 0 10 6"><path d="M1 1l4 4 4-4" fill="none" stroke="#fff" stroke-width="1.3"/></svg></span></div>

  <div class="chart-box" style="left:281px;top:305px;width:450px;height:148px">
    <svg width="450" height="148" viewBox="0 0 450 148" font-family="Ubuntu, sans-serif" font-size="7" fill="#888">
      <line x1="170" y1="19" x2="185" y2="19" stroke="#4a90d9" stroke-width="1.5"/><text x="188" y="21">Gross Rental Yield</text>
      <line x1="262" y1="19" x2="277" y2="19" stroke="#3a4fa0" stroke-width="1.5"/><text x="280" y="21">Forecast</text>
      <g stroke="#eeeeee">
        <line x1="35" y1="28" x2="440" y2="28"/><line x1="35" y1="59" x2="440" y2="59"/><line x1="35" y1="90" x2="440" y2="90"/><line x1="35" y1="120" x2="440" y2="120"/>
        <line x1="70" y1="28" x2="70" y2="120"/><line x1="112" y1="28" x2="112" y2="120"/><line x1="153" y1="28" x2="153" y2="120"/><line x1="195" y1="28" x2="195" y2="120"/><line x1="236" y1="28" x2="236" y2="120"/><line x1="278" y1="28" x2="278" y2="120"/><line x1="319" y1="28" x2="319" y2="120"/><line x1="361" y1="28" x2="361" y2="120"/><line x1="402" y1="28" x2="402" y2="120"/>
      </g>
      <text x="14" y="30">15%</text><text x="14" y="61">10%</text><text x="18" y="92">5%</text><text x="18" y="122">0%</text>
      <text x="62" y="132">1985</text><text x="104" y="132">1990</text><text x="145" y="132">1995</text><text x="187" y="132">2000</text><text x="228" y="132">2005</text><text x="270" y="132">2010</text><text x="311" y="132">2015</text><text x="353" y="132">2020</text><text x="394" y="132">2025</text>
      <polyline fill="none" stroke="#4a90d9" stroke-width="1.2" points="38,58 42,64 48,62 55,60 62,57 70,56 78,55 86,53 94,57 100,60 106,58 114,62 124,61 134,64 144,63 154,65 164,66 172,67 180,70 188,74 196,78 204,82 212,85 222,86 232,85 242,84 252,86 262,88 272,90 280,91 290,92 300,91 310,92 320,93 330,94 336,93"/>
      <line x1="336" y1="93" x2="440" y2="93" stroke="#3a4fa0" stroke-width="1.2"/>
    </svg>
  </div>
  <div class="note" style="left:281px;top:463px">By default we assume the ratio stays at thelatest value of 3.4%.You can change this assumption using the slider.</div>
  <div class="slider" style="left:281px;top:494px;width:452px"><div class="fill" style="width:44px"></div><div class="knob" style="left:40px"></div></div>

  <footer class="footer">© 2019 <span class="brand">Lark Hollow Funds</span>. All Right Reserved.</footer>
</section>

<!-- Step 5 -->
<section class="panel p5">
  <div class="track"></div>
  <div class="step done" style="left:59px"><div class="step-num">01</div><div class="step-dot"><svg width="10" height="10" viewBox="0 0 10 10"><path d="M2 5.2 4.2 7.4 8 3" fill="none" stroke="#0455a3" stroke-width="1.3"/></svg></div><div class="step-label" style="left:-79px">Property Type</div></div>
  <div class="step done" style="left:239px"><div class="step-num">02</div><div class="step-dot"><svg width="10" height="10" viewBox="0 0 10 10"><path d="M2 5.2 4.2 7.4 8 3" fill="none" stroke="#0455a3" stroke-width="1.3"/></svg></div><div class="step-label">Property Location</div></div>
  <div class="step done" style="left:408px"><div class="step-num">03</div><div class="step-dot"><svg width="10" height="10" viewBox="0 0 10 10"><path d="M2 5.2 4.2 7.4 8 3" fill="none" stroke="#0455a3" stroke-width="1.3"/></svg></div><div class="step-label">Property Valuation</div></div>
  <div class="step done" style="left:580px"><div class="step-num">04</div><div class="step-dot"><svg width="10" height="10" viewBox="0 0 10 10"><path d="M2 5.2 4.2 7.4 8 3" fill="none" stroke="#0455a3" stroke-width="1.3"/></svg></div><div class="step-label" style="left:-94px">Your Property Forecast</div></div>
  <div class="step active" style="left:752px"><div class="step-num">05</div><div class="step-dot"></div><div class="step-label" style="left:-99px;top:74px">Calculation</div></div>
  <div class="btn btn-outline" style="left:791px;width:94px">Privious</div>
  <div class="btn btn-primary" style="left:894px;width:99px">Recalculate</div>

  <div class="dash">
    <div class="dash-form">
      <div class="dash-row" style="top:0"><span class="lbl">Choose Property:</span><div class="dash-select">Sydney House</div></div>
      <div class="dash-row" style="top:26px"><span class="lbl">Choose Alternative Investment:</span><div class="dash-select">Global Shares</div></div>
      <div class="dash-row" style="top:54px"><span class="lbl">How much will the property cost? ⓘ</span>
        <div class="abs" style="left:143px;top:6px;width:130px;height:1px;background:#4a5158"></div>
        <div class="abs" style="left:143px;top:6px;width:32px;height:1px;background:#5d9fe0"></div>
        <div class="abs" style="left:172px;top:3px;width:6px;height:6px;border-radius:50%;border:1px solid #9cc7f0"></div>
        <span class="abs" style="left:283px;top:3px">$500,000</span></div>
      <div class="dash-row" style="top:80px"><span class="lbl">How much will you invest? ⓘ</span>
        <div class="abs" style="left:143px;top:6px;width:130px;height:1px;background:#4a5158"></div>
        <div class="abs" style="left:143px;top:6px;width:12px;height:1px;background:#5d9fe0"></div>
        <div class="abs" style="left:152px;top:3px;width:6px;height:6px;border-radius:50%;border:1px solid #9cc7f0"></div>
        <span class="abs" style="left:283px;top:3px">$200,000</span></div>
    </div>

    <div class="dash-chart" style="left:325px;width:230px">
      <svg width="230" height="108" viewBox="0 0 230 108" font-family="Ubuntu, sans-serif" font-size="5.5" fill="#aab">
        <text x="8" y="20">200K</text><text x="8" y="47">100K</text><text x="16" y="74">0</text><text x="6" y="100">-100K</text>
        <g stroke="#343b41"><line x1="25" y1="18" x2="225" y2="18"/><line x1="25" y1="45" x2="225" y2="45"/><line x1="25" y1="72" x2="225" y2="72"/><line x1="25" y1="98" x2="225" y2="98"/></g>
        <path d="M25 88 Q90 60 220 50" fill="none" stroke="#3a8ee6" stroke-width="1"/>
        <path d="M25 74 Q110 78 220 58" fill="none" stroke="#5ba8f0" stroke-width="1"/>
        <text x="62" y="62" fill="#3a8ee6">Shares</text><text x="155" y="64" fill="#5ba8f0">Property if no debt</text>
        <text x="28" y="106">2019</text><text x="64" y="106">2021</text><text x="100" y="106">2023</text><text x="136" y="106">2025</text><text x="172" y="106">2027</text><text x="206" y="106">2029</text>
      </svg>
    </div>

    <div class="dash-chart" style="left:567px;width:232px">
      <svg width="232" height="108" viewBox="0 0 232 108" font-family="Ubuntu, sans-serif" font-size="5.5" fill="#aab">
        <rect x="68" y="10" width="9" height="5" fill="#3a8ee6"/><text x="80" y="15">Shares Cashflow</text>
        <rect x="128" y="10" width="9" height="5" fill="#3a5bd6"/><text x="140" y="15">Property Cashflow</text>
        <text x="12" y="32">10K</text><text x="18" y="52">0</text><text x="8" y="74">-10K</text><text x="8" y="96">-20K</text>
        <g stroke="#343b41"><line x1="28" y1="30" x2="228" y2="30"/><line x1="28" y1="50" x2="228" y2="50"/><line x1="28" y1="72" x2="228" y2="72"/><line x1="28" y1="94" x2="228" y2="94"/></g>
        <g fill="#3a8ee6"><rect x="34" y="46" width="6" height="4"/><rect x="52" y="45" width="6" height="5"/><rect x="70" y="45" width="6" height="5"/><rect x="88" y="44" width="6" height="6"/><rect x="106" y="44" width="6" height="6"/><rect x="124" y="43" width="6" height="7"/><rect x="142" y="43" width="6" height="7"/><rect x="160" y="42" width="6" height="8"/><rect x="178" y="42" width="6" height="8"/><rect x="196" y="41" width="6" height="9"/><rect x="214" y="41" width="6" height="9"/></g>
        <g fill="#3a5bd6"><rect x="43" y="50" width="6" height="12"/><rect x="61" y="50" width="6" height="13"/><rect x="79" y="50" width="6" height="14"/><rect x="97" y="50" width="6" height="15"/><rect x="115" y="50" width="6" height="16"/><rect x="133" y="50" width="6" height="17"/><rect x="151" y="50" width="6" height="18"/><rect x="169" y="50" width="6" height="19"/><rect x="187" y="50" width="6" height="20"/><rect x="205" y="50" width="6" height="21"/></g>
        <text x="30" y="106">2019</text><text x="66" y="106">2021</text><text x="102" y="106">2023</text><text x="138" y="106">2025</text><text x="174" y="106">2027</text><text x="208" y="106">2029</text>
      </svg>
    </div>

    <div class="dash-sum">
      <div style="margin-top:12px">After 5 years:</div>
      <div class="small" style="margin-top:3px">Shares will return $82,431 more ⓘ</div>
      <div style="margin-top:12px">After 10 years:</div>
      <div class="small" style="margin-top:3px">Shares will return $160,176 more ⓘ</div>
      <div style="margin-top:5px">Debt Contribution ⓘ</div>
    </div>
  </div>

  <div class="note" style="left:0;width:100%;top:310px;text-align:center;line-height:17px">Note: These are indicative figures based on a boad range of assumption (below). Plese cotact Lark Hollow Funds or a financial planner before makin any investment based on the<br>assumtions from this calculato</div>

  <footer class="footer">© 2019 <span class="brand">Lark Hollow Funds</span>. All Right Reserved.</footer>
</section>

</body>
</html>
```